Velvet Meadow Hamper company needs a brochure design

We need a brochure design for a new company in Dubai called 'Velvet Meadow Hampers'. We already have a logo designed which I have attached and would like to use this and the green/gold/white colours for our brochure. Our company initially will be supplying Velvet Meadow Hamper wear of traditional wicker baskets in many designs which hold all the cutlery, crockery and accessories. We will also be selling picnic accessories. We want to purvey a sense of luxury and class in line with our logo. I have attached some photos of the picnicwear. As our products are changing all the time I thought a fold out cover which stays the same and then product cards inserted into the folder which can be changed according to our product changes. I am looking for a fairly simple design and each product card should have at least one photo of the product on it with a spec and description also. On the cover of the folder I would like room to write about the company and what we do, this can be inside or out and may or may not include photos. I have the logo designs in illustrator format and pdf. Please contact if any more information is needed.
Updates

Reason: I have extended this deadline as there are some content changes taking place.

Industry/Entity Type

It Company

```html
<!DOCTYPE html>
<html lang="en">
<head>
<meta charset="utf-8">
<title>Velvet Meadow Hampers – Folder Inner Panel</title>
<link href="https://fonts.googleapis.com/css2?family=Gelasio:wght@400;600&family=PT+Sans&display=swap" rel="stylesheet">
<style>
  :root {
    --paper: #ffffff;
    --ink-green: #1f3a1c;
    --brand-green: #1d3b1f;
    --gold: #c8902a;
    --mark: #222222;
  }
  html, body {
    margin: 0;
    padding: 0;
    width: 1200px;
    height: 969px;
    overflow: hidden;
    background: var(--paper);
  }
  .sheet {
    position: relative;
    width: 1200px;
    height: 969px;
    background: var(--paper);
  }
  .printer-marks {
    position: absolute;
    inset: 0;
  }
  .fold-label {
    position: absolute;
    font-family: "PT Sans", Arial, sans-serif;
    font-size: 8.5px;
    color: var(--mark);
    line-height: 1;
  }
  .fold-label--center { left: 514px; top: 0px; }
  .fold-label--up { left: 567px; top: 7px; }
  .fold-label--side { left: 1029px; top: 0px; }

  .welcome-panel {
    position: absolute;
    left: 115px;
    top: 0;
    width: 280px;
  }
  .brand-name {
    position: absolute;
    top: 103px;
    left: 0;
    margin: 0;
    white-space: nowrap;
    font-family: "Gelasio", Georgia, serif;
    font-weight: 600;
    font-size: 12px;
    letter-spacing: 0.16em;
    color: var(--brand-green);
  }
  .brand-dot {
    display: inline-block;
    width: 9px;
    height: 9px;
    border-radius: 50%;
    background: var(--brand-green);
    margin-right: 8px;
    vertical-align: 0;
  }
  .welcome-title {
    position: absolute;
    top: 179px;
    left: 0;
    margin: 0;
    white-space: nowrap;
    font-family: "Gelasio", Georgia, serif;
    font-weight: 400;
    font-size: 18.5px;
    color: var(--gold);
  }
  .welcome-copy {
    position: absolute;
    top: 226px;
    left: 0;
    width: 275px;
    font-family: "Gelasio", Georgia, serif;
    font-size: 11.2px;
    line-height: 13.1px;
    color: var(--ink-green);
  }
  .welcome-copy p {
    margin: 0 0 9px 0;
  }
</style>
</head>
<body>
<div class="sheet">
  <svg class="printer-marks" width="1200" height="969" viewBox="0 0 1200 969" aria-hidden="true">
    <g stroke="#222" stroke-width="0.8" fill="none">
      <!-- corner registration targets -->
      <g>
        <circle cx="15" cy="16" r="5"/>
        <line x1="6" y1="16" x2="24" y2="16"/><line x1="15" y1="7" x2="15" y2="25"/>
      </g>
      <g>
        <circle cx="1185" cy="16" r="5"/>
        <line x1="1176" y1="16" x2="1194" y2="16"/><line x1="1185" y1="7" x2="1185" y2="25"/>
      </g>
      <g>
        <circle cx="15" cy="953" r="5"/>
        <line x1="6" y1="953" x2="24" y2="953"/><line x1="15" y1="944" x2="15" y2="962"/>
      </g>
      <g>
        <circle cx="1185" cy="953" r="5"/>
        <line x1="1176" y1="953" x2="1194" y2="953"/><line x1="1185" y1="944" x2="1185" y2="962"/>
      </g>
      <!-- crop marks -->
      <line x1="30" y1="0" x2="30" y2="19"/><line x1="0" y1="30" x2="19" y2="30"/>
      <line x1="1169" y1="0" x2="1169" y2="19"/><line x1="1181" y1="30" x2="1200" y2="30"/>
      <line x1="30" y1="950" x2="30" y2="969"/><line x1="0" y1="938" x2="19" y2="938"/>
      <line x1="1169" y1="950" x2="1169" y2="969"/><line x1="1181" y1="938" x2="1200" y2="938"/>
      <!-- fold arrows -->
      <line x1="538" y1="10" x2="538" y2="20"/>
      <line x1="1045" y1="10" x2="1045" y2="20"/>
      <line x1="538" y1="947" x2="538" y2="958"/>
      <line x1="1045" y1="947" x2="1045" y2="958"/>
      <line x1="0" y1="722" x2="18" y2="722"/>
      <line x1="1181" y1="722" x2="1200" y2="722"/>
    </g>
    <g fill="#222">
      <polygon points="535.5,18 540.5,18 538,22"/>
      <polygon points="1042.5,18 1047.5,18 1045,22"/>
      <polygon points="535.5,949 540.5,949 538,945"/>
      <polygon points="1042.5,949 1047.5,949 1045,945"/>
      <polygon points="17,719.5 17,724.5 21,722"/>
      <polygon points="1182,719.5 1182,724.5 1178,722"/>
    </g>
  </svg>
  <span class="fold-label fold-label--center">Center Fold</span>
  <span class="fold-label fold-label--up">UP</span>
  <span class="fold-label fold-label--side">Side Fold</span>

  <section class="welcome-panel">
    <p class="brand-name"><span class="brand-dot"></span>VELVET MEADOW HAMPERS</p>
    <h1 class="welcome-title">Welcome to Velvet Meadow Hampers!</h1>
    <div class="welcome-copy">
      <p>The British love to picnic no matter what the weather and the picnic basket epitomises the British summer.&nbsp; Days spent relaxing with loved ones, dining ‘al fresco’ with a willow basket packed with delicious food is a great British tradition.</p>
      <p>Velvet Meadow Hampers offer a range of stylish traditional willow picnic hampers with a contemporary feel.&nbsp; Each basket comes equipped with cutlery, crockery and accessories, everything one would need for a perfect picnic. Having the highest ethical and ecological values, all our baskets are made from sustainable materials and individually handmade by Artisans.</p>
      <p>Alongside our range of picnic baskets we also offer a range of accessories from luxurious rugs to relax on, to stylish cool bags&nbsp; to keep your meals fresh.</p>
      <p>We at Velvet Meadow Hampers invite you to enjoy this classically English pastime!</p>
    </div>
  </section>
</div>
</body>
</html>
```